Business Card Design Project

We are a construction company in Orange County, CA. We need a two sided business card. We would like the back to be our logo with web URL. Front should included Name, title, address, phone, fax and email address.

our address is
627 West Dorrance Blvd, Suite 308
Anaheim, CA 92718

Our logo files are attached.

Construction

```html
<!DOCTYPE html>
<html lang="en">
<head>
<meta charset="utf-8">
<title>Kelmar Business Card – Front and Back</title>
<link rel="stylesheet" href="https://fonts.googleapis.com/css2?family=Source+Sans+3:wght@400;600;700;800&display=swap">
<style>
  :root {
    --brand-blue: #1b4e80;
    --ink: #4a4a4a;
    --ink-soft: #5a5a5a;
    --card: #ffffff;
    --backdrop: #ece7e1;
    --divider: #bdbdbd;
  }
  * { box-sizing: border-box; margin: 0; padding: 0; }
  html, body {
    width: 1200px; height: 410px; overflow: hidden;
    background: var(--backdrop);
    font-family: "Source Sans 3", "Helvetica Neue", Arial, sans-serif;
  }
  .stage { position: relative; width: 1200px; height: 410px; }
  .card {
    position: absolute; top: 62px;
    width: 525px; height: 299px;
    background: var(--card);
    border-radius: 14px;
    overflow: hidden;
    box-shadow: 0 1px 3px rgba(0,0,0,.25);
  }
  .card--front { left: 42px; }
  .card--back { left: 609px; }

  .wordmark {
    position: absolute; left: 0; right: 0;
    text-align: center;
    color: var(--brand-blue);
    font-weight: 800;
    font-size: 84px;
    line-height: 1;
    letter-spacing: -1px;
  }
  .card--front .wordmark { top: 28px; }
  .card--back .wordmark { top: 92px; }

  .address {
    position: absolute; right: 277px; top: 146px;
    text-align: right;
    color: var(--ink-soft);
    font-size: 14px; line-height: 22px;
  }
  .divider {
    position: absolute; left: 265px; top: 146px;
    width: 1px; height: 74px;
    background: var(--divider);
  }
  .contact-list {
    position: absolute; left: 284px; top: 146px;
    list-style: none;
    color: var(--ink-soft);
    font-size: 14px; line-height: 18px;
  }
  .contact-list li { display: flex; align-items: center; gap: 6px; }
  .contact-list svg { width: 10px; height: 10px; fill: var(--ink); flex: none; }

  .footer-band { position: absolute; left: 0; bottom: 0; width: 525px; height: 45px; }
  .name-title {
    position: absolute; right: 67px; bottom: 14px;
    color: #fff; font-size: 18px; line-height: 1;
  }
  .name-title strong { font-weight: 700; }

  .website {
    position: absolute; left: 0; right: 0; top: 200px;
    text-align: center;
    color: var(--ink);
    font-size: 14px; letter-spacing: 2.4px;
  }
</style>
</head>
<body>
<main class="stage">

  <section class="card card--front" aria-label="Business card front">
    <div class="wordmark">KELMAR</div>

    <address class="address" style="font-style:normal">
      627 West Dorrance Blvd<br>
      Suite 308, Anaheim<br>
      CA&nbsp; 92718
    </address>

    <div class="divider"></div>

    <ul class="contact-list">
      <li>
        <svg viewBox="0 0 10 10" aria-hidden="true"><path d="M2 0.5 L3.6 2.6 L2.7 3.6 Q3.6 5.6 6.4 7.3 L7.4 6.4 L9.5 8 L8.2 9.5 Q3.5 9 0.5 1.8 Z"/></svg>
        01-234-5678
      </li>
      <li>
        <svg viewBox="0 0 10 10" aria-hidden="true"><path d="M2 1 H7 V3.5 H9 Q10 3.5 10 4.5 V8.5 H0 V4.5 Q0 3.5 1 3.5 H2 Z M3 2 V3.5 H6 V2 Z M2 5.5 V6.5 H4 V5.5 Z"/></svg>
        01-234-5678
      </li>
      <li>
        <svg viewBox="0 0 10 10" aria-hidden="true"><path d="M0.5 2 H9.5 V8 H0.5 Z" /><path d="M0.5 2 L5 5.5 L9.5 2" stroke="#fff" stroke-width="0.9" fill="none"/></svg>
        info@kelmarbuild.com
      </li>
      <li>
        <svg viewBox="0 0 10 10" aria-hidden="true"><circle cx="5" cy="5" r="4.5"/><path d="M0.5 5 H9.5 M5 0.5 Q2 5 5 9.5 Q8 5 5 0.5" stroke="#fff" stroke-width="0.8" fill="none"/></svg>
        www.kelmarbuild.com
      </li>
    </ul>

    <svg class="footer-band" viewBox="0 0 525 45" aria-hidden="true">
      <defs>
        <linearGradient id="steel-strip" x1="0" x2="1" y1="0" y2="0">
          <stop offset="0" stop-color="#141414"/>
          <stop offset="1" stop-color="#c4c4c4"/>
        </linearGradient>
      </defs>
      <polygon points="0,1 256,1 245,12 0,12" fill="url(#steel-strip)"/>
      <polygon points="0,16 244,16 262,0 525,0 525,45 0,45" fill="var(--brand-blue)"/>
    </svg>
    <p class="name-title"><strong>Your Name,</strong> Title</p>
  </section>

  <section class="card card--back" aria-label="Business card back">
    <div class="wordmark">KELMAR</div>
    <p class="website">www.kelmarbuild.com</p>
  </section>

</main>
</body>
</html>
```